Home Security Company Business Card

Looking for a eye catching business card that is non traditional and stands out but yet still looks professional. It should include all the pertinent information such as name, title, address, telephone, e-mail, website address should definitely stand out and then finally the logo.

Target Market(s)

Residential and Commercial accounts mostly upscale accounts

Industry/Entity Type

Security

Contact Information for Business Card

Name
Title
Address
Office #
Cell #
E-mail
Website

Font styles to use
Serif
Sans Serif

Requirements
Must have
• Logo, two sided color configuration
Nice to have
• You decide
Should not have
• There really aren't any.

```html
<!DOCTYPE html>
<html lang="en">
<head>
<meta charset="utf-8">
<title>Bastion Security Systems – Business Card</title>
<link href="https://fonts.googleapis.com/css2?family=Tinos&family=Marcellus&display=swap" rel="stylesheet">
<style>
  :root {
    --backdrop: #efe2c6;
    --burgundy: #7a1416;
    --gold: #e2b03c;
    --paper: #ffffff;
    --ink-light: #ffffff;
    --shadow: rgba(60, 30, 10, 0.35);
  }
  * { margin: 0; padding: 0; box-sizing: border-box; }
  html, body { width: 1189px; height: 1200px; overflow: hidden; }
  body { background: var(--backdrop); position: relative; font-family: "Marcellus", "Optima", sans-serif; }

  .card {
    position: absolute;
    left: 167px;
    width: 855px;
    height: 487px;
    border-radius: 20px;
    overflow: hidden;
    box-shadow: 8px 10px 14px var(--shadow);
  }
  .card--front { top: 69px; background: var(--burgundy); }
  .card--back { top: 627px; background: var(--paper); }

  .wordmark { position: absolute; font-family: "Tinos", "Times New Roman", serif; font-weight: 400; text-align: center; line-height: 1; }
  .wordmark__name { display: block; letter-spacing: -1px; }
  .wordmark__sub { display: block; letter-spacing: -1px; }

  .card--front .wordmark { left: 0; right: 0; top: 185px; color: var(--ink-light); }
  .card--front .wordmark__name { font-size: 78px; }
  .card--front .wordmark__sub { font-size: 40px; margin-top: -4px; }

  .back-shape { position: absolute; inset: 0; }

  .contact { position: absolute; left: 34px; top: 78px; color: var(--ink-light); }
  .contact__name { font-size: 35px; line-height: 1; font-weight: 400; letter-spacing: 0.3px; }
  .contact__title { font-size: 19px; letter-spacing: 1px; margin-top: 2px; }
  .contact__address { font-size: 22px; line-height: 30px; margin-top: 34px; letter-spacing: 0.5px; }
  .contact__lines { list-style: none; margin-top: 12px; font-size: 22px; line-height: 28px; letter-spacing: 0.5px; }
  .contact__lines li { display: flex; align-items: center; gap: 14px; }
  .contact__lines svg { width: 22px; height: 22px; flex: none; }
  .contact__web { font-size: 22px; margin-top: 28px; letter-spacing: 1px; }

  .card--back .wordmark { left: 440px; width: 372px; top: 268px; color: var(--burgundy); }
  .card--back .wordmark__name { font-size: 50px; }
  .card--back .wordmark__sub { font-size: 26px; margin-top: -2px; }
  .brand-dot { position: absolute; left: 586px; top: 120px; width: 120px; height: 120px; border-radius: 50%; background: var(--gold); }
</style>
</head>
<body>
  <section class="card card--front" aria-label="Card front">
    <h1 class="wordmark">
      <span class="wordmark__name">BASTION</span>
      <span class="wordmark__sub">SECURITY SYSTEMS INC.</span>
    </h1>
  </section>

  <section class="card card--back" aria-label="Card back">
    <svg class="back-shape" viewBox="0 0 855 487" width="855" height="487" aria-hidden="true">
      <path d="M0 0 H432 Q330 243 432 487 H0 Z" fill="var(--gold)"/>
      <path d="M0 0 H426 Q345 243 426 487 H0 Z" fill="var(--burgundy)"/>
    </svg>

    <div class="contact">
      <h2 class="contact__name">Marcus Hale</h2>
      <p class="contact__title">Managing Director</p>
      <p class="contact__address">PO Box your address<br>2nd Lane, USA</p>
      <ul class="contact__lines">
        <li>
          <svg viewBox="0 0 22 22" aria-label="Office"><rect x="1" y="1" width="20" height="20" rx="3" fill="#fff"/><path d="M5 9 Q11 4 17 9 L15 10 Q11 8 7 10 Z M7 11 H15 L16 16 H6 Z" fill="var(--burgundy)"/><circle cx="11" cy="13.5" r="1.5" fill="#fff"/></svg>
          <span>555-014-2280</span>
        </li>
        <li>
          <svg viewBox="0 0 22 22" aria-label="Mobile"><rect x="4" y="1" width="14" height="20" rx="3" fill="#fff"/><rect x="7" y="4" width="8" height="7" fill="var(--burgundy)"/><rect x="7" y="13" width="8" height="5" fill="var(--burgundy)" opacity="0.6"/></svg>
          <span>+1 555-014-2281</span>
        </li>
        <li>
          <svg viewBox="0 0 22 22" aria-label="Email"><rect x="1" y="3" width="20" height="16" rx="2" fill="#fff"/><rect x="3.5" y="5.5" width="15" height="11" fill="none" stroke="var(--burgundy)" stroke-width="1.4"/><path d="M3.5 5.5 L11 12 L18.5 5.5 M3.5 16.5 L9 11 M18.5 16.5 L13 11" fill="none" stroke="var(--burgundy)" stroke-width="1.4"/></svg>
          <span>info@bastionsecure.com</span>
        </li>
      </ul>
      <p class="contact__web">www.bastionsecure.com</p>
    </div>

    <span class="brand-dot" aria-hidden="true"></span>
    <h2 class="wordmark">
      <span class="wordmark__name">BASTION</span>
      <span class="wordmark__sub">SECURITY SYSTEMS INC.</span>
    </h2>
  </section>
</body>
</html>
```